PAX

We need to design a power point presentation that can englobe all our company products.

This presentation has to have all the required to be used as template for future presentations.

We focus on prodcut developing for supermarkets, ( we help them with their own brand products ex. Sunny Harvest, TK, etc.)
Also we are on the marine industry, we develop ships and oil rigs for the Oil and deep water market.

Target Market(s)

Oil Companies
Supermarket companies
Retail Companies

Industry/Entity Type

It Company

Requirements
Must have
• Our Logo and company colors
Nice to have
• Something describing globalization.
Should not have
• Orange color

```html
<!DOCTYPE html>
<html lang="en">
<head>
<meta charset="utf-8">
<title>PAX – Presentation Slide</title>
<link rel="stylesheet" href="https://fonts.googleapis.com/css2?family=Michroma&family=Arimo:wght@400&display=swap">
<style>
  :root {
    --brand-blue: #0a5fb4;
    --brand-blue-deep: #0b3f94;
    --header-blue: #1348a8;
    --header-blue-light: #2c6fd0;
    --heading-blue: #0d62b5;
    --body-ink: #1a1a1a;
    --paper: #ffffff;
    --accent-green: #7cc242;
    --tab-shadow: rgba(0, 0, 0, 0.28);
  }
  html, body {
    margin: 0;
    padding: 0;
    overflow: hidden;
    background: var(--paper);
  }
  .slide {
    position: relative;
    width: 1200px;
    height: 900px;
    overflow: hidden;
    background: var(--paper);
  }
  .header-band {
    position: absolute;
    left: 0; top: 0;
    width: 1200px; height: 117px;
    background: linear-gradient(90deg, var(--header-blue) 0%, var(--header-blue-light) 55%, var(--header-blue) 100%);
  }
  .project-title {
    position: absolute;
    left: 42px; top: 40px;
    margin: 0;
    font-family: "Michroma", sans-serif;
    font-size: 38px;
    font-weight: 400;
    letter-spacing: 1px;
    color: var(--paper);
    -webkit-text-stroke: 1px var(--paper);
  }
  .logo-tab {
    position: absolute;
    left: 1008px; top: -20px;
    width: 147px; height: 226px;
    background: linear-gradient(180deg, #ffffff 0%, #f1f3f6 100%);
    border-radius: 0 0 74px 74px;
    box-shadow: 0 4px 10px var(--tab-shadow);
    display: flex;
    flex-direction: column;
    align-items: center;
    justify-content: center;
    gap: 10px;
    padding-top: 20px;
    box-sizing: border-box;
  }
  .logo-dot {
    width: 52px; height: 52px;
    border-radius: 50%;
    background: var(--brand-blue);
  }
  .logo-name {
    font-family: "Michroma", sans-serif;
    font-size: 34px;
    color: var(--accent-green);
    line-height: 1;
  }
  .content {
    position: absolute;
    left: 40px; top: 0;
    width: 850px;
  }
  .section {
    position: absolute;
    left: 0;
    width: 850px;
  }
  .section-heading {
    margin: 0;
    font-family: "Michroma", sans-serif;
    font-size: 31px;
    font-weight: 400;
    color: var(--heading-blue);
    -webkit-text-stroke: 0.8px var(--heading-blue);
    line-height: 1;
  }
  .section-body {
    margin: 20px 0 0;
    font-family: "Arimo", sans-serif;
    font-size: 21.5px;
    line-height: 36px;
    color: var(--body-ink);
  }
  .section--one { top: 163px; }
  .section--two { top: 374px; }
  .section--three { top: 600px; }
  .photo-ring {
    position: absolute;
    left: 993px;
    width: 174px; height: 174px;
  }
  .photo-ring--rig { top: 265px; }
  .photo-ring--cruise { top: 477px; }
  .photo-ring--refinery { top: 691px; }
  .footer-band {
    position: absolute;
    left: 0; top: 828px;
    width: 1200px; height: 72px;
    background: var(--brand-blue);
  }
</style>
</head>
<body>
<main class="slide">
  <header class="header-band" role="img" aria-label="Blue world map background suggesting global reach">
    <h1 class="project-title">PROJECT TITLE HERE</h1>
  </header>

  <div class="logo-tab" aria-label="PAX logo">
    <span class="logo-dot"></span>
    <span class="logo-name">PAX</span>
  </div>

  <section class="content">
    <article class="section section--one">
      <h2 class="section-heading">Content Heading Here</h2>
      <p class="section-body">Sub content here Sub content here Sub content here Sub content here Sub content here Sub content here Sub content here Sub content here Sub content here Sub content here Sub content here Sub content here Sub content here</p>
    </article>
    <article class="section section--two">
      <h2 class="section-heading">Content Heading Here</h2>
      <p class="section-body">Sub content here Sub content here Sub content here Sub content here Sub content here Sub content here Sub content here Sub content here Sub content here Sub content here Sub content here Sub content here Sub content here</p>
    </article>
    <article class="section section--three">
      <h2 class="section-heading">Content Heading Here</h2>
      <p class="section-body">Sub content here Sub content here Sub content here Sub content here Sub content here Sub content here Sub content here Sub content here Sub content here Sub content here Sub content here Sub content here Sub content here</p>
    </article>
  </section>

  <svg class="photo-ring photo-ring--rig" viewBox="0 0 174 174" role="img" aria-label="Photo of an offshore supply vessel beside an oil rig at sea">
    <defs>
      <linearGradient id="rig-fill" x1="0" y1="0" x2="0" y2="1">
        <stop offset="0" stop-color="#9cc3e6"/>
        <stop offset="0.5" stop-color="#c8664a"/>
        <stop offset="1" stop-color="#2f5f88"/>
      </linearGradient>
    </defs>
    <circle cx="87" cy="87" r="82" fill="url(#rig-fill)" stroke="var(--brand-blue-deep)" stroke-width="8"/>
  </svg>

  <svg class="photo-ring photo-ring--cruise" viewBox="0 0 174 174" role="img" aria-label="Photo of a white cruise ship on blue sea">
    <defs>
      <linearGradient id="cruise-fill" x1="0" y1="0" x2="0" y2="1">
        <stop offset="0" stop-color="#4f8fd0"/>
        <stop offset="0.5" stop-color="#e8eef4"/>
        <stop offset="1" stop-color="#123f7a"/>
      </linearGradient>
    </defs>
    <circle cx="87" cy="87" r="82" fill="url(#cruise-fill)" stroke="var(--brand-blue-deep)" stroke-width="8"/>
  </svg>

  <svg class="photo-ring photo-ring--refinery" viewBox="0 0 174 174" role="img" aria-label="Photo of a refinery structure silhouetted at dusk">
    <defs>
      <linearGradient id="refinery-fill" x1="0" y1="0" x2="0" y2="1">
        <stop offset="0" stop-color="#4a6a8a"/>
        <stop offset="0.55" stop-color="#1d2b3a"/>
        <stop offset="1" stop-color="#b0706a"/>
      </linearGradient>
    </defs>
    <circle cx="87" cy="87" r="82" fill="url(#refinery-fill)" stroke="var(--brand-blue-deep)" stroke-width="8"/>
  </svg>

  <footer class="footer-band"></footer>
</main>
</body>
</html>
```